Recycling company need a brochure - We are metal and electronic recycling company, we need a broc...

We need to illustrate our e-scrap services and values to our costumers in this brochure. We are collecting and recycling electronic waste. We are sorting, and dismanteling the goods to maximize value of the goods. We are using color green on business cards and on our trucks and containers, so brochure should also have green, we are a green business. It should communicate that doing business with us is; simple, easy to establish relations, quick transport service and
enviromental friendly. More info: www.brovendalt.dk

Target Market(s)

Companies with used electronic for scrap / Try go to www.brovendalt.dk to get more info.

Industry/Entity Type

Recycling

Font styles to use
Serif

Requirements
Must have
• Key services:
• Pick up service / Logistics
• Fast report
• Data destruction
• Fast payment
• AAA Credit-logo
• ISO14001 Certifikat-logo
• Company Logo
Nice to have
• Please browse the uploaded pictures, and use your favourites

```html
<!DOCTYPE html>
<html lang="en">
<head>
<meta charset="utf-8">
<title>Brovendalt – E-scrap services</title>
<link href="https://fonts.googleapis.com/css2?family=Work+Sans:wght@500;600;700&display=swap" rel="stylesheet">
<style>
  :root{
    --paper:#efefed;
    --ring:#c1c5bd;
    --green-deep:#004a2f;
    --green-mid:#1f8a44;
    --green-light:#76bd43;
    --green-title:#238b45;
    --green-ring:#3cb54a;
    --ink:#1a1a1a;
    --aaa-red:#d52b1e;
  }
  *{margin:0;padding:0;box-sizing:border-box}
  html,body{width:1200px;height:850px;overflow:hidden;background:var(--paper)}
  body{font-family:"Work Sans",Arial,sans-serif;color:var(--ink)}
  .brochure{position:relative;width:1200px;height:850px;overflow:hidden;background:var(--paper)}
  .ring-decoration{position:absolute;left:513px;top:28px;width:834px;height:834px;border-radius:50%;
    background:radial-gradient(circle at center,var(--paper) 0,var(--paper) 47%,var(--ring) 53%,var(--ring) 92%,var(--paper) 100%)}
  .waves{position:absolute;inset:0}
  .feature-icon{position:absolute}
  .feature-title{position:absolute;color:var(--green-title);font-weight:700;line-height:1.22}
  .feature-body{position:absolute;font-weight:600;font-size:17px;line-height:23px;border-left:4px solid var(--green-light);padding-left:13px}
  .report-title{left:152px;top:96px;font-size:35px}
  .payment-title{left:162px;top:460px;font-size:35px}
  .policy-title{left:538px;top:140px;font-size:34px;line-height:1.03}
  .data-title{left:820px;top:106px;width:350px;text-align:center;font-size:35px;line-height:1}
  .report-body{left:52px;top:204px;width:330px}
  .payment-body{left:52px;top:568px;width:330px}
  .policy-body{left:444px;top:230px;width:340px;line-height:25px}
  .data-body{left:842px;top:358px;width:320px;font-size:18px;line-height:25.7px}
  .gap{height:23px}
  .policy-body .gap{height:25px}
  .photo-frame{position:absolute;left:973px;top:191px;width:240px;height:138px;border:3px solid var(--green-mid);border-right:none;border-radius:0 0 0 50px;background:var(--paper)}
  .photo-frame .photo{position:absolute;left:5px;top:6px;right:12px;bottom:6px;background:linear-gradient(135deg,#5e6660,#8d9490 45%,#3f5a45 75%,#6a6f6b)}
  .badge{position:absolute}
  .iso-badge{left:680px;top:515px;width:80px;height:80px;border-radius:50%;background:var(--green-mid);border:5px solid #fff;box-shadow:0 0 0 2px var(--green-mid)}
  .credit-badge{left:303px;top:778px;width:72px;height:40px;background:var(--aaa-red)}
</style>
</head>
<body>
<main class="brochure">
  <div class="ring-decoration" role="img" aria-label="Large grey recycling-arrow ring decoration"></div>

  <svg class="waves" width="1200" height="850" viewBox="0 0 1200 850" aria-hidden="true">
    <path d="M0 0H1200V20H760C600 20 450 48 300 58C180 66 80 72 0 72Z" fill="var(--green-deep)"/>
    <path d="M290 44C420 30 520 0 600 0H770C720 30 640 55 520 60C430 63 350 56 290 44Z" fill="var(--green-light)"/>
    <path d="M330 42C430 30 520 8 610 0H700C640 20 560 38 470 44C420 47 370 46 330 42Z" fill="var(--green-mid)"/>
    <path d="M560 850C620 800 720 780 850 790C980 800 1060 800 1200 770V850Z" fill="var(--green-light)"/>
    <path d="M800 850C880 810 980 800 1080 795C1130 792 1170 780 1200 770V850Z" fill="var(--green-mid)" opacity=".85"/>
    <path d="M0 827H620C580 835 570 842 565 850H0Z" fill="var(--green-deep)"/>
    <path d="M900 850C980 815 1080 800 1200 768V850Z" fill="var(--green-deep)"/>
  </svg>

  <!-- Fast report -->
  <svg class="feature-icon" style="left:44px;top:90px" width="94" height="94" viewBox="0 0 94 94" aria-hidden="true">
    <circle cx="47" cy="47" r="42" fill="none" stroke="var(--green-ring)" stroke-width="8"/>
    <rect x="22" y="22" width="44" height="46" rx="4" fill="var(--green-light)" stroke="var(--green-mid)" stroke-width="3"/>
    <g stroke="var(--green-mid)" stroke-width="3"><line x1="36" y1="34" x2="58" y2="34"/><line x1="36" y1="43" x2="58" y2="43"/><line x1="36" y1="52" x2="54" y2="52"/></g>
    <g fill="none" stroke="var(--green-mid)" stroke-width="2"><rect x="27" y="31" width="5" height="5"/><rect x="27" y="40" width="5" height="5"/><rect x="27" y="49" width="5" height="5"/></g>
    <line x1="50" y1="72" x2="72" y2="48" stroke="var(--green-ring)" stroke-width="5"/>
  </svg>
  <h2 class="feature-title report-title">Fast<br>Report</h2>
  <div class="feature-body report-body">
    The weight can be determined on<br>our truck scale or a scale near you,<br>&nbsp;whichever suits you best. However<br>a scale near your collection point<br>will<br>make the process faster and offers<br>you greater security as the weight<br>can<br>&nbsp;be agreed on with both parties<br>present.
  </div>

  <!-- Fast payment -->
  <svg class="feature-icon" style="left:43px;top:451px" width="106" height="106" viewBox="0 0 106 106" aria-hidden="true">
    <circle cx="53" cy="53" r="47" fill="none" stroke="var(--green-ring)" stroke-width="9"/>
    <circle cx="58" cy="38" r="15" fill="var(--ink)"/>
    <text x="58" y="45" text-anchor="middle" font-family="Work Sans,Arial,sans-serif" font-weight="700" font-size="20" fill="#fff">$</text>
    <rect x="21" y="58" width="9" height="18" fill="var(--ink)"/>
    <path d="M34 60H55C60 60 60 66 55 66H46H58L74 57C79 55 82 60 78 63L60 76H34Z" fill="var(--ink)"/>
  </svg>
  <h2 class="feature-title payment-title">Fast<br>Payment</h2>
  <div class="feature-body payment-body">
    Brovendalt.dk always keep<br>favorable iron and metal prices.
    <div class="gap"></div>
    We constantly follow commodity<br>prices to ensure updated prices.
    <div class="gap"></div>
    To better assist you with metal<br>scrap in large quantities,<br>&nbsp;we suggest contacting us by<br>e-mail or telephone.
  </div>
  <div class="badge credit-badge" role="img" aria-label="Credit rating badge"></div>

  <!-- Environmental policy -->
  <svg class="feature-icon" style="left:436px;top:121px" width="94" height="94" viewBox="0 0 94 94" aria-hidden="true">
    <circle cx="47" cy="47" r="42" fill="#fff" stroke="var(--green-ring)" stroke-width="8"/>
    <path d="M20 60L34 50H52C56 50 56 56 52 56H44L66 48C71 47 73 52 69 54L46 70H30L24 68Z" fill="var(--ink)"/>
    <line x1="50" y1="50" x2="50" y2="26" stroke="var(--ink)" stroke-width="3"/>
    <path d="M50 36C42 36 38 30 38 26C45 26 50 30 50 36Z" fill="var(--ink)"/>
    <path d="M50 32C57 32 61 26 61 22C54 22 50 26 50 32Z" fill="var(--ink)"/>
    <path d="M50 44C58 44 62 40 62 36C55 36 50 40 50 44Z" fill="var(--ink)"/>
  </svg>
  <h2 class="feature-title policy-title">Environmental<br>Policy</h2>
  <div class="feature-body policy-body">
    The products we receive for<br>recycling are resold to<br>environmentally approved players in<br>the Danish,<br>as well as on the international<br>market.
    <div class="gap"></div>
    We focus a lot on the fact that the<br>process of extraction<br>of raw materials has the right time,<br>from end to end.
  </div>
  <div class="badge iso-badge" role="img" aria-label="Environmental certificate badge"></div>

  <!-- Data destruction -->
  <h2 class="feature-title data-title">Safe destruction of<br>DATA</h2>
  <div class="photo-frame">
    <div class="photo" role="img" aria-label="Photo of shredded hard drives and circuit boards"></div>
  </div>
  <div class="feature-body data-body">
    Brovendalt.dk offers a large<br>number of methods that ensure<br>your company that all personal<br>information is destroyed.<br>Physical destruction of hard<br>drives<br>Image documentation on the<br>destruction of hard drives<br>Reports that document the<br>number of hard disks for<br>destruction
  </div>
</main>
</body>
</html>
```